Consulting company business cards

We have a base design, but would be willing to update. We have a new logo/"tag" that needs to be added. Current business card design is attached for reference into our "style."

Industry/Entity Type

Business

Contact Information for Business Card

Should contain name and title, office number, mobile number if appropriate, e-mail, website, physical address, and company logo.

Font styles to use
Other font styles liked:
• See current card design on KorvandBCard

Colors
0455a3
85acd3
aaaaaa

Requirements
Must have
• Our colors are navy blue, gray, and a lighter blue
Nice to have
• Design that I can easily drop in new names/titles as we hire employees.

```html
<!DOCTYPE html>
<html lang="en">
<head>
<meta charset="utf-8">
<title>Brenlow Business Card</title>
<link rel="stylesheet" href="https://fonts.googleapis.com/css2?family=Oswald:wght@600&family=PT+Sans:wght@400;700&display=swap">
<style>
  :root {
    --page-bg: #d9dcdf;
    --card-bg: #eef1f2;
    --card-edge: #dfe3e6;
    --navy: #1f3a4f;
    --title-blue: #4a86b8;
    --body-text: #2a3540;
    --art-dark: #2d5c72;
    --art-mid: #3b6f86;
  }
  html, body {
    margin: 0;
    padding: 0;
    width: 1200px;
    height: 969px;
    overflow: hidden;
    background: var(--page-bg);
  }
  .business-card {
    position: absolute;
    left: 80px;
    top: 188px;
    width: 1040px;
    height: 592px;
    background: var(--card-bg);
    border: 1px solid var(--card-edge);
    border-radius: 30px;
    overflow: hidden;
    box-shadow: 0 10px 30px rgba(0,0,0,0.12);
  }
  .mascot-art {
    position: absolute;
    left: 440px;
    top: 0;
    width: 600px;
    height: 592px;
    background: linear-gradient(160deg, var(--art-mid), var(--art-dark));
    border-radius: 300px 0 0 0;
  }
  .brand {
    position: absolute;
    left: 63px;
    top: 66px;
    display: flex;
    align-items: center;
    gap: 14px;
  }
  .brand-name {
    font-family: "Oswald", sans-serif;
    font-weight: 600;
    font-size: 72px;
    line-height: 1;
    letter-spacing: 2px;
    color: var(--navy);
  }
  .brand-mark {
    width: 44px;
    height: 44px;
    border-radius: 50%;
    background: var(--navy);
  }
  .tagline {
    position: absolute;
    left: 63px;
    top: 162px;
    font-family: "PT Sans", sans-serif;
    font-size: 19px;
    letter-spacing: 2.2px;
    text-transform: uppercase;
    color: var(--body-text);
  }
  .person-name {
    position: absolute;
    left: 63px;
    top: 204px;
    font-family: "PT Sans", sans-serif;
    font-weight: 700;
    font-size: 32px;
    color: var(--navy);
  }
  .person-title {
    position: absolute;
    left: 63px;
    top: 248px;
    font-family: "PT Sans", sans-serif;
    font-size: 29px;
    color: var(--title-blue);
  }
  .contact-block {
    position: absolute;
    left: 63px;
    font-family: "PT Sans", sans-serif;
    font-size: 25px;
    line-height: 36px;
    color: var(--body-text);
    margin: 0;
  }
  .address { top: 302px; }
  .phones { top: 388px; }
  .web-contact { top: 460px; }
</style>
</head>
<body>
  <div class="business-card">
    <div class="mascot-art" role="img" aria-label="Large dog head illustration in profile"></div>

    <div class="brand">
      <span class="brand-name">BRENLOW</span>
      <span class="brand-mark"></span>
    </div>
    <div class="tagline">A Cloud Consulting Company</div>

    <div class="person-name">Danakorvand</div>
    <div class="person-title">Office Manager</div>

    <p class="contact-block address">1850 W 41st ST<br>Westfield Ohio 43190</p>
    <p class="contact-block phones">O 555.014.6382<br>F 555.014.6399</p>
    <p class="contact-block web-contact">dkorvand@brenlowtech.com<br>www.brenlowtech.com</p>
  </div>
</body>
</html>
```